Heritage Hollow Business Cards

Require a business card design. <br/><br/>Needs to include logo (either round or long version) plus these details:<br/>Maya Torvell<br/>Heritage Hollow<br/>maya@kelvadtrading.com.au<br/>02 6481 7395<br/>PO Box Glenwarra NSW 2791<br/>www.heritagehollow.com.au<br/><br/>I need in an editable format so that I can create for multiple staff members. <br/><br/>

Target Market(s)

We are an online store selling renovation products to home owners are builders. Looking for a classic classy design.

Industry/Entity Type

Home And Garden

Contact Information for Business Card

Maya Torvell
Heritage Hollow
maya@kelvadtrading.com.au
02 6481 7395
PO Box Glenwarra NSW 2791
www.heritagehollow.com.au

Colors

Designer to choose colors to be used in the design.

Requirements
Must have
• Must include Logo.

```html
<!DOCTYPE html>
<html lang="en">
<head>
<meta charset="utf-8">
<title>Heritage Hollow Business Cards</title>
<link href="https://fonts.googleapis.com/css2?family=Roboto:wght@400;500;700&display=swap" rel="stylesheet">
<style>
  :root {
    --backdrop: #e4e4e2;
    --card-dark: #1f1b1b;
    --gold: #c99a2e;
    --gold-light: #e6c467;
    --card-light: #f7f7f6;
    --ink: #2a2a2a;
    --ink-soft: #444;
    --green: #2f5a45;
    --ghost: #e2e4e2;
  }
  * { box-sizing: border-box; margin: 0; padding: 0; }
  html, body {
    width: 1200px; height: 1021px; overflow: hidden;
    background: var(--backdrop);
    font-family: "Roboto", sans-serif;
  }
  .card {
    position: absolute; left: 250px; width: 700px; height: 400px;
    box-shadow: 0 10px 30px rgba(0,0,0,.18);
    overflow: hidden;
  }
  .card-front { top: 70px; background: var(--card-dark); }
  .card-back { top: 540px; background: var(--card-light); }

  .front-emblem {
    position: absolute; left: 50%; top: 50%;
    width: 230px; height: 230px; margin: -115px 0 0 -115px;
    border: 2px solid var(--gold); border-radius: 50%;
    display: flex; align-items: center; justify-content: center;
  }
  .front-emblem .brand-name {
    color: var(--gold); font-size: 30px; font-weight: 500;
    text-align: center; line-height: 1.1;
  }

  .back-decoration {
    position: absolute; left: -150px; top: 110px;
    width: 420px; height: 420px; border-radius: 50%;
    border: 4px solid var(--ghost);
  }
  .person { position: absolute; left: 48px; top: 48px; }
  .person-name { color: var(--green); font-size: 24px; font-weight: 700; letter-spacing: .5px; }
  .person-role { color: var(--ink-soft); font-size: 15px; margin-top: 2px; }

  .back-brand {
    position: absolute; right: 60px; top: 120px;
    color: var(--ink); font-size: 34px; font-weight: 500;
  }

  .contact {
    position: absolute; left: 380px; top: 215px;
    color: var(--ink); font-size: 19px; line-height: 1.3;
  }
  .address { margin-bottom: 14px; }
  .contact-line { display: flex; align-items: center; gap: 8px; }
  .contact-line svg { width: 16px; height: 16px; flex: none; fill: var(--ink-soft); }
</style>
</head>
<body>
  <section class="card card-front">
    <div class="front-emblem">
      <span class="brand-name">Heritage<br>Hollow</span>
    </div>
  </section>

  <section class="card card-back">
    <div class="back-decoration"></div>
    <div class="person">
      <div class="person-name">MAYA TORVELL</div>
      <div class="person-role">OWNER</div>
    </div>
    <div class="back-brand">Heritage Hollow</div>
    <div class="contact">
      <div class="address">PO Box Glenwarra<br>NSW 2791</div>
      <div class="contact-line">
        <svg viewBox="0 0 24 24" aria-hidden="true"><path d="M6.6 10.8a15.1 15.1 0 0 0 6.6 6.6l2.2-2.2c.3-.3.7-.4 1-.2 1.1.4 2.3.6 3.6.6.6 0 1 .4 1 1V20c0 .6-.4 1-1 1A17 17 0 0 1 3 4c0-.6.4-1 1-1h3.5c.6 0 1 .4 1 1 0 1.3.2 2.5.6 3.6.1.3 0 .7-.2 1z"/></svg>
        <span>02 6481 7395</span>
      </div>
      <div class="contact-line">
        <svg viewBox="0 0 24 24" aria-hidden="true"><path d="M2 5h20v14H2zm2 2v.5l8 5 8-5V7zm0 2.8V17h16V9.8l-8 5z"/></svg>
        <span>maya@kelvadtrading.com.au</span>
      </div>
      <div class="contact-line">
        <svg viewBox="0 0 24 24" aria-hidden="true"><path d="M12 2a10 10 0 1 0 0 20 10 10 0 0 0 0-20zm6.9 6h-2.9a15 15 0 0 0-1.4-3.6A8 8 0 0 1 18.9 8zM12 4c.8 1.2 1.5 2.5 1.9 4h-3.8c.4-1.5 1.1-2.8 1.9-4zM4.3 14a8 8 0 0 1 0-4h3.4a16 16 0 0 0 0 4zm.8 2h2.9c.3 1.3.8 2.5 1.4 3.6A8 8 0 0 1 5.1 16zM8 8H5.1a8 8 0 0 1 4.3-3.6C8.8 5.5 8.3 6.7 8 8zm4 12c-.8-1.2-1.5-2.5-1.9-4h3.8c-.4 1.5-1.1 2.8-1.9 4zm2.3-6H9.7a14 14 0 0 1 0-4h4.6a14 14 0 0 1 0 4zm.3 5.6c.6-1.1 1.1-2.3 1.4-3.6h2.9a8 8 0 0 1-4.3 3.6zm1.7-5.6a16 16 0 0 0 0-4h3.4a8 8 0 0 1 0 4z"/></svg>
        <span>www.heritagehollow.com.au</span>
      </div>
    </div>
  </section>
</body>
</html>
```